Business Card Design for Marketing Firm

Looking for business card design for higher end marketing firm. Clean but impressionable/trendy. We are a marketing firm that represents manufacturers in the foodservice equipment and supply industry. Our customers are end users such has hotels, restaurants, country clubs, convention centers and casinos as well as distributors of restaurants supplies and equipment, and manufacturers of foodservice equipment and supplies.
Target Market(s)
Hotels, Restaurants, Supply & Equipment Distributors, Foodservice Manufacturers
Industry/Entity Type
Foodservice/Hospitality
Contact Information for Business Card
Name, Title, Contact Number, Email, Website, Social Media, Address
Requirements
Must have
- Clean & Simple but Serious and Impressionable

```html
<!DOCTYPE html>
<html lang="en">
<head>
<meta charset="utf-8">
<title>Meridian Service Reps – Business Card</title>
<link rel="stylesheet" href="https://fonts.googleapis.com/css2?family=EB+Garamond:wght@400;500;700&display=swap">
<style>
  :root {
    --navy: #03037f;
    --white: #ffffff;
    --silver: #b9bcc8;
    --ink-grey: #3a3a3a;
    --backdrop: #7a7a7a;
  }
  * { margin: 0; padding: 0; box-sizing: border-box; }
  html, body { width: 1200px; height: 821px; overflow: hidden; }
  body {
    background: var(--backdrop);
    font-family: "EB Garamond", Georgia, serif;
    display: flex;
    align-items: center;
    justify-content: center;
    gap: 48px;
  }
  .card {
    position: relative;
    width: 540px;
    height: 309px;
    background: var(--navy);
    overflow: hidden;
    box-shadow: 0 10px 24px rgba(0,0,0,0.3);
  }
  .card-wave { position: absolute; inset: 0; }
  .brand {
    position: absolute;
    left: 56px;
    top: 44px;
    display: flex;
    align-items: center;
    gap: 10px;
    color: var(--navy);
    font-weight: 500;
    font-size: 21px;
    letter-spacing: 0.06em;
    text-transform: uppercase;
  }
  .brand-dot {
    width: 12px; height: 12px;
    border-radius: 50%;
    background: var(--navy);
  }
  .person { position: absolute; left: 56px; top: 90px; }
  .person-name {
    color: var(--navy);
    font-weight: 700;
    font-size: 30px;
    letter-spacing: 0.04em;
    text-transform: uppercase;
    line-height: 1;
  }
  .person-title {
    color: var(--ink-grey);
    font-size: 17px;
    margin-top: 4px;
  }
  .contact {
    position: absolute;
    right: 26px;
    bottom: 24px;
    list-style: none;
    color: var(--white);
    text-align: right;
    font-size: 14px;
    line-height: 1.3;
  }
  .contact li {
    display: flex;
    justify-content: flex-end;
    align-items: center;
    gap: 9px;
  }
  .contact-phone { font-size: 16px; margin-top: 2px; }
  .contact svg { width: 12px; height: 12px; flex: none; fill: var(--white); }
  .contact .icon-spacer { width: 12px; }
  .card-back { display: flex; align-items: center; justify-content: center; }
  .back-brand {
    display: flex;
    align-items: center;
    gap: 16px;
    color: var(--silver);
    font-weight: 500;
    font-size: 30px;
    letter-spacing: 0.08em;
    text-transform: uppercase;
  }
  .back-brand-dot {
    width: 18px; height: 18px;
    border-radius: 50%;
    background: var(--silver);
  }
</style>
</head>
<body>
  <section class="card card-front">
    <svg class="card-wave" viewBox="0 0 540 309" aria-hidden="true">
      <path fill="var(--white)" d="M0,0 H540 V250 C528,190 485,172 390,174 C270,176 120,196 55,170 C22,156 10,128 0,104 Z"/>
    </svg>
    <div class="brand"><span class="brand-dot"></span>Meridian Service Reps</div>
    <div class="person">
      <div class="person-name">Dana Whitlock</div>
      <div class="person-title">Founder &amp; CEO</div>
    </div>
    <ul class="contact">
      <li>4471 Harbor Lane<span class="icon-spacer"></span></li>
      <li>Milford, CT 06460
        <svg viewBox="0 0 12 12"><path d="M6 0a4 4 0 0 0-4 4c0 3 4 8 4 8s4-5 4-8a4 4 0 0 0-4-4zm0 5.6A1.6 1.6 0 1 1 6 2.4a1.6 1.6 0 0 1 0 3.2z"/></svg></li>
      <li class="contact-phone">(555) 240-7319
        <svg viewBox="0 0 12 12"><path d="M2.5 0.5l2 2.3-1 1.4c.6 1.5 1.8 2.7 3.3 3.3l1.4-1 2.3 2-1 2.2C5 10.5 1.5 7 .3 1.5z"/></svg></li>
      <li>hello@meridianreps.com
        <svg viewBox="0 0 12 12"><path d="M0 2h12v8H0zm1 1v.4l5 3.2 5-3.2V3zm0 1.6V9h10V4.6L6 7.8z"/></svg></li>
      <li>meridianreps.com
        <svg viewBox="0 0 12 12"><path d="M6 0a6 6 0 1 0 0 12A6 6 0 0 0 6 0zm0 1c.9 0 1.8 2 1.9 4.5H4.1C4.2 3 5.1 1 6 1zM1 6.5h2.1C3.2 8.4 3.7 10 4.3 10.7A5 5 0 0 1 1 6.5zm0-1A5 5 0 0 1 4.3 1.3C3.7 2 3.2 3.6 3.1 5.5zm5 5.5c-.9 0-1.8-2-1.9-4.5h3.8C7.8 9 6.9 11 6 11zm1.7-.3c.6-.7 1.1-2.3 1.2-4.2H11a5 5 0 0 1-3.3 4.2zM8.9 5.5C8.8 3.6 8.3 2 7.7 1.3A5 5 0 0 1 11 5.5z"/></svg></li>
    </ul>
  </section>

  <section class="card card-back">
    <div class="back-brand"><span class="back-brand-dot"></span>Meridian Service Reps</div>
  </section>
</body>
</html>
```